Business Cards Needed for Innovative Healthcare Marketing Company

We are a marketing company focused on healthcare. Our company is all about rebranding yourself renewing your image and generating results. The phoenix stands for "reborn" or "rising" which we provide new brands for our clients we take their old brands and renew it with creativity and innovation. I am looking for a business card with color dimension. I have attached an example of a card I think has the look and feel of what I am trying to accomplish. I like that the card example has black and grey font colors, I like the font placement and the small logo, I really like the use of the colors on the right those are the colors of my logo. My logo is phoenix so maybe incorporating flames similar to that design. I would like the back a solid color maybe red with an opaque version of the logo and website. As a marketing company I am always open to creative liberty!

Target Market(s)

Doctors and business professionals.

Industry/Entity Type

Marketing

Contact Information for Business Card

Valcorne Health Care Marketing
Marla Tenwick- CEO
#(512)638-2974
email-marla@valcorne.com
website- valcorne.com

Font styles to use
Sans Serif

Colors
ec1f27
f37122
ffc214
fbed22
fbf289
f04a50

Requirements
Must have
• The logo and required information
Nice to have
• icons by the information
Should not have
• child like font

```html
<!DOCTYPE html>
<html lang="en">
<head>
<meta charset="utf-8">
<title>Valcorne Health Care Marketing – Business Card</title>
<link rel="stylesheet" href="https://fonts.googleapis.com/css2?family=Quicksand:wght@500;600;700&display=swap">
<style>
  :root {
    --page-bg: #e7e4e2;
    --card-light: #f6f2f0;
    --card-light-edge: #e9e2df;
    --wine: #8a1a20;
    --wine-deep: #6e1217;
    --wine-bright: #a52a2e;
    --flame: #e8662a;
    --flame-soft: #f0873a;
    --brand-red: #b23a2e;
    --text-light: #f3e6e2;
    --text-soft: #e9c9c0;
  }
  * { margin: 0; padding: 0; box-sizing: border-box; }
  html, body {
    width: 1200px; height: 969px; overflow: hidden;
    background: var(--page-bg);
    font-family: "Quicksand", "Helvetica Neue", Arial, sans-serif;
  }
  .business-card {
    position: absolute; left: 100px; top: 201px;
    width: 1000px; height: 567px;
    border-radius: 34px; overflow: hidden;
    background: linear-gradient(160deg, var(--card-light) 0%, var(--card-light-edge) 100%);
    box-shadow: 0 18px 40px rgba(60, 30, 30, 0.18);
  }
  .card-waves { position: absolute; inset: 0; width: 100%; height: 100%; }
  .brand {
    position: absolute; left: 52px; top: 52px;
    display: flex; align-items: center; gap: 36px;
  }
  .brand-mark {
    width: 150px; height: 150px; border-radius: 50%;
    background: var(--brand-red);
  }
  .brand-name {
    color: var(--brand-red); font-weight: 600;
    letter-spacing: 2px; line-height: 1;
  }
  .brand-name .word { display: block; font-size: 66px; }
  .brand-name .tagline {
    display: block; font-size: 22px; letter-spacing: 1.5px;
    margin-top: 14px; padding-top: 8px;
    border-top: 2px solid var(--brand-red);
  }
  .holder { position: absolute; left: 77px; top: 440px; }
  .holder-name {
    color: var(--flame-soft); font-size: 35px; font-weight: 600;
    letter-spacing: 1.5px; line-height: 1;
  }
  .holder-role {
    color: var(--text-soft); font-size: 25px; font-weight: 600;
    letter-spacing: 1px; margin-top: 14px;
  }
  .contact-list {
    position: absolute; right: 52px; top: 400px;
    list-style: none; text-align: right;
  }
  .contact-item {
    display: flex; justify-content: flex-end; align-items: center; gap: 18px;
    color: var(--text-soft); font-size: 25px; font-weight: 500;
    letter-spacing: 1px; height: 39px;
  }
  .contact-icon { width: 22px; height: 22px; fill: var(--flame); flex: none; }
</style>
</head>
<body>
  <div class="business-card">
    <svg class="card-waves" viewBox="0 0 1000 567" preserveAspectRatio="none" aria-hidden="true">
      <defs>
        <linearGradient id="wineFill" x1="0" y1="0" x2="1" y2="1">
          <stop offset="0" stop-color="var(--wine-bright)"/>
          <stop offset="0.55" stop-color="var(--wine)"/>
          <stop offset="1" stop-color="var(--wine-deep)"/>
        </linearGradient>
      </defs>
      <path d="M0 368 C 300 400, 640 300, 1000 92 L1000 118 C 650 320, 320 420, 0 392 Z" fill="var(--flame)"/>
      <path d="M0 398 C 320 428, 660 326, 1000 128 L1000 567 L0 567 Z" fill="url(#wineFill)"/>
    </svg>

    <div class="brand">
      <div class="brand-mark"></div>
      <div class="brand-name">
        <span class="word">VALCORNE</span>
        <span class="tagline">HEALTH CARE MARKETING</span>
      </div>
    </div>

    <div class="holder">
      <p class="holder-name">MARLA TENWICK</p>
      <p class="holder-role">CEO</p>
    </div>

    <ul class="contact-list">
      <li class="contact-item">(512)638-2974
        <svg class="contact-icon" viewBox="0 0 24 24" aria-hidden="true"><path d="M6.6 10.8a15.1 15.1 0 0 0 6.6 6.6l2.2-2.2a1 1 0 0 1 1-.25 11.4 11.4 0 0 0 3.6.57 1 1 0 0 1 1 1V20a1 1 0 0 1-1 1A17 17 0 0 1 3 4a1 1 0 0 1 1-1h3.5a1 1 0 0 1 1 1c0 1.25.2 2.45.57 3.57a1 1 0 0 1-.25 1z"/></svg>
      </li>
      <li class="contact-item">MARLA@VALCORNE.COM
        <svg class="contact-icon" viewBox="0 0 24 24" aria-hidden="true"><path d="M2 5h20v14H2z M3.5 6.5 12 13l8.5-6.5" fill="var(--flame)" stroke="var(--wine)" stroke-width="1.4"/></svg>
      </li>
      <li class="contact-item">WWW.VALCORNE.COM
        <svg class="contact-icon" viewBox="0 0 24 24" aria-hidden="true"><circle cx="12" cy="12" r="10"/><path d="M2 12h20M12 2c3 3 3 17 0 20M12 2c-3 3-3 17 0 20" fill="none" stroke="var(--wine)" stroke-width="1.4"/></svg>
      </li>
    </ul>
  </div>
</body>
</html>
```